New Business Card Design Project

We require a business card design for Vexalund, a newly established Indian company.
Our focus is on the development, manufacturing, and export of a diverse array of pharmaceutical products on a global scale. The card should convey a professional appearance, as our primary markets are in Africa, China, and Southeast Asian nations.
We envision a two-sided business card, with the reverse side dedicated to a logo set against a solid color or an elegantly designed pattern. The corners should be rounded. We would appreciate seeing both horizontal and vertical design options. We trust the designer to utilize their expertise in creating this design.

The content for the business card is included in the attached Word file.

Target Market(s)

Our primary markets are in Africa, China, and Southeast Asian, Latin America, Maldives, Sri Lanka

Industry/Entity Type

Pharmaceutical Manufacturing and Export

Contact Information for Business Card

Colors

Designer to choose colors to be used in the design.

Requirements
Must have
• The reverse side of the business card features solely the logo along with the tagline, "Healing for All."
Should not have
• The logo should not exceed two instances, encompassing both the front and back sides of the card.

```html
<!DOCTYPE html>
<html lang="en">
<head>
<meta charset="utf-8">
<title>Vexalund Business Card</title>
<link rel="stylesheet" href="https://fonts.googleapis.com/css2?family=Montserrat:wght@400;500;700&display=swap">
<style>
  :root {
    --backdrop: #3a3a3c;
    --card: #ffffff;
    --brand-blue: #27a6df;
    --brand-coral: #ef5e4a;
    --text-grey: #555555;
    --pattern-grey: #eeeeee;
  }
  * { margin: 0; padding: 0; box-sizing: border-box; }
  html, body { width: 1200px; height: 987px; overflow: hidden; }
  body {
    background: var(--backdrop);
    font-family: 'Montserrat', sans-serif;
    position: relative;
  }
  .card {
    position: absolute;
    width: 700px;
    height: 400px;
    background: var(--card);
    border-radius: 12px;
    overflow: hidden;
    box-shadow: 0 18px 40px rgba(0,0,0,0.45);
  }
  .card-back { left: 60px; top: 60px; }
  .card-front { left: 440px; top: 527px; }

  /* back side */
  .back-pattern {
    position: absolute; inset: 0;
    background: radial-gradient(ellipse at center, #ffffff 20%, var(--pattern-grey) 100%);
  }
  .back-brand {
    position: absolute; left: 0; right: 0; top: 150px;
    display: flex; align-items: center; justify-content: center; gap: 14px;
  }
  .brand-dot {
    width: 22px; height: 22px; border-radius: 50%;
    background: var(--brand-coral);
  }
  .brand-name {
    font-weight: 700; color: var(--brand-blue);
    font-size: 56px; letter-spacing: 1px; line-height: 1;
  }
  .tagline {
    position: absolute; left: 0; right: 0; top: 318px;
    text-align: center; font-weight: 700; font-size: 17px;
    color: var(--brand-blue); letter-spacing: 0.5px;
  }
  .tagline .accent { color: var(--brand-coral); }

  /* front side */
  .front-brand {
    position: absolute; left: 48px; top: 44px;
    font-size: 54px;
  }
  .contact-block { position: absolute; left: 64px; top: 150px; }
  .person-name {
    font-weight: 700; color: var(--brand-blue); font-size: 24px; letter-spacing: 0.5px;
  }
  .person-role {
    color: var(--text-grey); font-size: 17px; margin-top: 2px;
  }
  .address {
    color: var(--text-grey); font-size: 17px; line-height: 1.3; margin-top: 22px;
  }
  .contact-list { list-style: none; margin-top: 22px; }
  .contact-list li {
    display: flex; align-items: center; gap: 12px;
    color: var(--text-grey); font-size: 18px; line-height: 1.35;
  }
  .contact-list svg { width: 16px; height: 16px; flex: none; }
  .mark-area {
    position: absolute; right: 0; top: 0; width: 300px; height: 400px;
    background: linear-gradient(120deg, #ffffff 0%, rgba(39,166,223,0.55) 45%, rgba(239,94,74,0.55) 100%);
  }
</style>
</head>
<body>

<section class="card card-back" aria-label="Card reverse side">
  <div class="back-pattern" role="img" aria-label="Faint repeating brand pattern background"></div>
  <div class="back-brand">
    <span class="brand-dot"></span>
    <span class="brand-name">Vexalund</span>
  </div>
  <p class="tagline">Healing <span class="accent">for All.</span></p>
</section>

<section class="card card-front" aria-label="Card front side">
  <div class="mark-area" role="img" aria-label="Large brand decoration in blue and coral"></div>
  <div class="brand-name front-brand">Vexalund</div>
  <div class="contact-block">
    <p class="person-name">Rohan K. Vartak</p>
    <p class="person-role">CEO</p>
    <p class="address">12, Lotus Park, Ravipur<br>441200, India</p>
    <ul class="contact-list">
      <li>
        <svg viewBox="0 0 16 16" aria-hidden="true"><rect x="4" y="1" width="8" height="14" rx="1.5" fill="none" stroke="#ef5e4a" stroke-width="1.6"/><circle cx="8" cy="12.3" r="0.9" fill="#ef5e4a"/></svg>
        +919876501234
      </li>
      <li>
        <svg viewBox="0 0 16 16" aria-hidden="true"><rect x="1" y="3" width="14" height="10" fill="#ef5e4a"/><path d="M1 3 L8 9 L15 3" fill="none" stroke="#fff" stroke-width="1.3"/></svg>
        rvartak@vexalund.com
      </li>
      <li>
        <svg viewBox="0 0 16 16" aria-hidden="true"><g fill="none" stroke="#ef5e4a" stroke-width="1.3"><circle cx="8" cy="8" r="6.5"/><ellipse cx="8" cy="8" rx="3" ry="6.5"/><path d="M1.5 8 H14.5 M2.5 4.8 H13.5 M2.5 11.2 H13.5"/></g></svg>
        vexalund.com
      </li>
    </ul>
  </div>
</section>

</body>
</html>
```